Moravel Aesthetic Doctor

I require an elegant, luxurious looking business card for my aesthetic business. I am a doctor and that will set me aside from competitors. I am planning to provide home and spa based treatments to clients with high expectations. I have attached my logo.

```html
<!DOCTYPE html>
<html lang="en">
<head>
<meta charset="utf-8">
<title>Moravel Aesthetic Doctor – Business Card</title>
<link href="https://fonts.googleapis.com/css2?family=Montserrat:wght@400;500&family=Lato:wght@400&display=swap" rel="stylesheet">
<style>
  :root {
    --bg: #e4e4e4;
    --card: #ffffff;
    --blue: #2b8fd2;
    --blue-light: #5bb4e4;
    --blue-pale: #a9dcf3;
    --blue-deep: #1f6fb8;
    --text: #4a4a4a;
    --text-soft: #666666;
    --rule: #3a9ad9;
  }
  * { box-sizing: border-box; margin: 0; padding: 0; }
  html, body { width: 1200px; height: 896px; overflow: hidden; }
  body { background: var(--bg); position: relative; font-family: "Montserrat", sans-serif; color: var(--text); }

  .card {
    position: absolute; left: 302px; width: 619px; height: 354px;
    background: var(--card); box-shadow: 0 2px 6px rgba(0,0,0,.18);
  }
  .card--front { top: 94px; }
  .card--back { top: 469px; }

  /* Front */
  .hero-art {
    position: absolute; left: 0; top: 32px; width: 340px; height: 302px;
    background: linear-gradient(100deg, var(--blue-pale) 0%, var(--blue-light) 45%, var(--blue) 75%, var(--blue-deep) 100%);
    border-radius: 0 60% 45% 0 / 0 50% 50% 0;
  }
  .brand-front {
    position: absolute; right: 33px; top: 254px; text-align: center;
    color: var(--blue-light); font-weight: 400;
  }
  .brand-front .brand-name { font-size: 40px; letter-spacing: 3px; line-height: 1; }
  .brand-front .brand-tag { font-size: 16px; letter-spacing: 1.5px; margin-top: 8px; }

  /* Back */
  .brand-back {
    position: absolute; left: 55px; top: 140px; display: flex; align-items: center; gap: 10px;
    color: var(--blue-light); font-weight: 400;
  }
  .brand-mark { width: 66px; height: 66px; border: 2px solid #9a9a9a; border-radius: 50%; }
  .brand-back .brand-name { font-size: 33px; letter-spacing: 2px; line-height: 1; }
  .brand-back .brand-tag { font-size: 13px; letter-spacing: 1.2px; margin-top: 5px; }

  .divider { position: absolute; left: 319px; top: 92px; width: 1px; height: 172px; background: var(--rule); }

  .details { position: absolute; left: 337px; top: 86px; }
  .doctor-name { font-size: 17px; color: var(--blue); font-weight: 400; }
  .doctor-name .postnominals { font-size: 9.5px; color: var(--text); margin-left: 2px; }
  .credential, .service-type { font-size: 14px; line-height: 18px; }
  .credential { margin-top: 4px; }
  .service-type { margin-top: 11px; }
  .contact-list { list-style: none; margin-top: 12px; font-size: 14px; }
  .contact-list li { display: flex; align-items: center; gap: 8px; height: 18px; }
  .contact-list svg { width: 11px; height: 11px; flex: none; fill: var(--blue); }
  .social { display: inline-flex; gap: 9px; margin-left: 20px; }
  .social span { width: 11px; height: 11px; border-radius: 50%; background: var(--blue); }

  .services {
    position: absolute; left: 0; right: 0; top: 311px; text-align: center;
    font-family: "Lato", sans-serif; font-size: 14px; color: var(--text-soft);
  }
</style>
</head>
<body>
  <section class="card card--front">
    <div class="hero-art" role="img" aria-label="Illustration of a profile with flowing blue hair ribbons"></div>
    <div class="brand-front">
      <div class="brand-name">MORAVEL</div>
      <div class="brand-tag">AESTHETIC DOCTOR</div>
    </div>
  </section>

  <section class="card card--back">
    <div class="brand-back">
      <div class="brand-mark"></div>
      <div>
        <div class="brand-name">MORAVEL</div>
        <div class="brand-tag">AESTHETIC DOCTOR</div>
      </div>
    </div>

    <div class="divider"></div>

    <div class="details">
      <p class="doctor-name">Dr Elena Varga <span class="postnominals">MRCPCH MD</span></p>
      <p class="credential">Australasian Diploma<br>of Aesthetic Medicine</p>
      <p class="service-type">Home and Spa<br>Based Treatments</p>
      <ul class="contact-list">
        <li>
          <svg viewBox="0 0 12 12" aria-hidden="true"><path d="M2.5 0.5l2 2.3-1 1.2c.7 1.5 1.9 2.8 3.5 3.5l1.2-1 2.3 2-1 2C5 10.5 1.5 7 0.5 1.5z"/></svg>
          0800 555 014
        </li>
        <li>
          <svg viewBox="0 0 12 12" aria-hidden="true"><path d="M0 2.5h12v7H0z M0.6 3l5.4 3.6L11.4 3" stroke="#fff" stroke-width=".8"/></svg>
          elena@moravel.co.nz
        </li>
        <li>
          <svg viewBox="0 0 12 12" aria-hidden="true"><circle cx="6" cy="6" r="5.5"/><path d="M.5 6h11M6 .5v11M2 3h8M2 9h8" stroke="#fff" stroke-width=".6" fill="none"/><ellipse cx="6" cy="6" rx="2.4" ry="5.5" stroke="#fff" stroke-width=".6" fill="none"/></svg>
          www.moravel.co.nz
          <span class="social"><span></span><span></span></span>
        </li>
      </ul>
    </div>

    <p class="services">Dermal injectables - Plasma facials - Microneedling Skin boosters - Excessive sweating</p>
  </section>
</body>
</html>
```